Business Card Design Project

Looking for a logo and business card for a Real State Business i will be opening. The name is not choosen yet , but will probably be RWT IMOVEIS.
I was thinking black and silver colors, but am open to nice ideas.
I did add a business card that i liked a lot, am looking for something like that, with logo in black or silver in a black card. The logo i was thinking in the letters RWT as i uploaded or something or little and cute buildings or a house...just ideas, can be any nice logo.
Updates

You guys can add other colors if you want, I like colors very "BRIGHT" and "open", like red, pink, strong colors. almost glow in the dark colors. lol

Designers,

I've increased more 88 dollars in the budget for 1st place cause I will want envelope designs... small and big sizes.

So 1st place is now U$248,00. 

No need to send the envelope designs right now... only the business cards designs.

Thank you.

Industry/Entity Type

Business

Requirements
Must have
• Marcela Tavares Rocha

www.RWTimoveis-exemplo.com.br

+554187316042

marcela@rwtimoveis-exemplo.com.br

```html
<!DOCTYPE html>
<html lang="pt-BR">
<head>
<meta charset="utf-8">
<title>RWT Imoveis – Cartão de visita</title>
<link href="https://fonts.googleapis.com/css2?family=Arimo:wght@400;700&display=swap" rel="stylesheet">
<style>
  :root {
    --backdrop: #262626;
    --card-light: #f2f2f2;
    --card-dark: #050505;
    --ink: #1a1a1a;
    --ink-soft: #333333;
    --accent: #8cc63f;
    --silver: #d9d9d9;
    --muted: #bdbdbd;
  }
  * { box-sizing: border-box; margin: 0; padding: 0; }
  html, body {
    width: 1200px;
    height: 900px;
    overflow: hidden;
    background: var(--backdrop);
    font-family: "Arimo", Arial, sans-serif;
  }
  .stage {
    position: relative;
    width: 1200px;
    height: 900px;
  }
  .card {
    position: absolute;
    width: 560px;
    height: 320px;
    box-shadow: 0 18px 40px rgba(0,0,0,0.55);
  }

  /* Front: contact side */
  .card-front {
    left: 140px;
    top: 120px;
    background: var(--card-light);
    color: var(--ink);
  }
  .card-front .brand {
    position: absolute;
    left: 56px;
    top: 70px;
    display: flex;
    align-items: center;
    gap: 12px;
  }
  .brand-square {
    width: 16px;
    height: 16px;
    background: var(--accent);
  }
  .card-front .brand-name {
    font-weight: 700;
    font-size: 40px;
    letter-spacing: 0.5px;
    color: var(--ink);
  }
  .holder-name {
    position: absolute;
    left: 56px;
    top: 170px;
    font-weight: 700;
    font-size: 16px;
    letter-spacing: 1.5px;
    text-transform: uppercase;
    color: var(--ink);
  }
  .contact-list {
    position: absolute;
    left: 56px;
    top: 204px;
    list-style: none;
    font-size: 14px;
    line-height: 21px;
    color: var(--ink-soft);
  }
  .contact-list li {
    display: flex;
    align-items: center;
    gap: 10px;
  }
  .contact-list li::before {
    content: "";
    width: 4px;
    height: 4px;
    border-radius: 50%;
    background: var(--accent);
  }
  .highlight { color: var(--accent); font-weight: 700; }

  /* Back: brand side */
  .card-back {
    left: 500px;
    top: 460px;
    background: var(--card-dark);
    color: var(--silver);
  }
  .card-back .brand {
    position: absolute;
    right: 52px;
    top: 108px;
    display: flex;
    align-items: center;
    gap: 16px;
  }
  .card-back .brand-square {
    width: 22px;
    height: 22px;
  }
  .card-back .brand-name {
    font-weight: 700;
    font-size: 56px;
    letter-spacing: 0.5px;
    color: var(--silver);
  }
  .site-url {
    position: absolute;
    right: 52px;
    top: 196px;
    font-size: 14px;
    letter-spacing: 4.5px;
    text-transform: uppercase;
    color: var(--muted);
  }
</style>
</head>
<body>
  <main class="stage">
    <section class="card card-front" aria-label="Frente do cartão">
      <div class="brand">
        <span class="brand-square"></span>
        <span class="brand-name">RWT IMOVEIS</span>
      </div>
      <p class="holder-name">Marcela Tavares Rocha</p>
      <ul class="contact-list">
        <li>+554187316042</li>
        <li><span><span class="highlight">marcela</span>@rwtimoveis-exemplo.com.br</span></li>
        <li><span>www.<span class="highlight">RWTimoveis-exemplo</span>.com.br</span></li>
      </ul>
    </section>

    <section class="card card-back" aria-label="Verso do cartão">
      <div class="brand">
        <span class="brand-square"></span>
        <span class="brand-name">RWT IMOVEIS</span>
      </div>
      <p class="site-url">www.rwtimoveis-exemplo.com.br</p>
    </section>
  </main>
</body>
</html>
```